Zielgruppe
Immobilienmakler
Aufgabenstellung
Top moderne hochwertige Visitenkate, wir hätten gerne eine sehr hochwertig moderne Visitenkarte mit Bild vom Mitarbeiter... Anbei habe ich die alte Visitenkarte die ich sehr kindlich finde... Es sollte jetzt sehr exklusive aussehen. Alle Daten können von der alten Visitenkarte übernommen werden.. danke

```html
<!DOCTYPE html>
<html lang="de">
<head>
<meta charset="utf-8">
<title>Velta Agentur – Visitenkarte</title>
<link rel="stylesheet" href="https://fonts.googleapis.com/css2?family=Mulish:wght@400;800&display=swap">
<style>
  :root {
    --backdrop: #2d2d2b;
    --paper: #ffffff;
    --forest: #013118;
    --ink: #1f1f1f;
    --ring: #efefef;
    --photo-tone: #dfe3e8;
  }
  * { margin: 0; padding: 0; box-sizing: border-box; }
  html, body {
    width: 935px; height: 1200px; overflow: hidden;
    background: var(--backdrop);
    font-family: "Mulish", "Avenir Next", sans-serif;
  }
  .card {
    position: absolute;
    width: 541px; height: 350px;
    background: var(--paper);
    box-shadow: 14px 18px 30px rgba(0,0,0,0.45);
    overflow: hidden;
  }
  .card--front { left: 208px; top: 198px; }
  .card--back { left: 214px; top: 670px; }

  .company-name {
    position: absolute;
    color: var(--ink);
    font-weight: 800;
    white-space: nowrap;
  }
  .card--front .company-name {
    left: 0; width: 541px; top: 148px;
    text-align: center; font-size: 40px; line-height: 50px;
  }
  .card--back .company-name {
    left: 0; width: 266px; top: 290px;
    text-align: center; font-size: 20px; line-height: 26px;
  }

  .portrait-ring {
    position: absolute; left: 57px; top: 59px;
    width: 138px; height: 138px; border-radius: 50%;
    background: var(--ring);
    box-shadow: 0 4px 10px rgba(0,0,0,0.18), inset 0 0 6px rgba(0,0,0,0.08);
  }
  .portrait {
    position: absolute; left: 14px; top: 14px;
    width: 110px; height: 110px; border-radius: 50%;
    background: radial-gradient(circle at 50% 40%, #f3f5f8 0%, var(--photo-tone) 70%, #c9ced6 100%);
  }

  .info-panel {
    position: absolute; left: 266px; top: 0;
    width: 275px; height: 350px;
    background: var(--forest);
    color: var(--paper);
  }
  .info-panel__notch { position: absolute; left: 0; top: 72px; }
  .person { position: absolute; left: 50px; top: 70px; }
  .person__name { font-size: 19px; font-weight: 800; line-height: 24px; }
  .person__role { font-size: 14.5px; font-weight: 400; line-height: 18px; margin-top: 3px; }

  .contact { position: absolute; left: 0; width: 275px; font-size: 14.5px; line-height: 18px; }
  .contact__icon { position: absolute; left: 22px; top: 1px; width: 16px; height: 16px; }
  .contact__text { position: absolute; left: 54px; top: 0; white-space: nowrap; }
</style>
</head>
<body>

<section class="card card--front">
  <div class="company-name">Velta Agentur</div>
</section>

<section class="card card--back">
  <div class="portrait-ring">
    <div class="portrait" role="img" aria-label="Porträtfoto des Mitarbeiters im weißen Hemd"></div>
  </div>
  <div class="company-name">Velta Agentur</div>

  <div class="info-panel">
    <svg class="info-panel__notch" width="20" height="24" viewBox="0 0 20 24"><polygon points="0,0 20,12 0,24" fill="#ffffff"/></svg>

    <div class="person">
      <div class="person__name">Lukas Brandner</div>
      <div class="person__role">Dipl. Immobilienmanager<br>Geschäftsführer</div>
    </div>

    <div class="contact" style="top:187px">
      <svg class="contact__icon" viewBox="0 0 16 16"><path d="M8 1a5 5 0 0 0-5 5c0 3.6 5 9 5 9s5-5.4 5-9a5 5 0 0 0-5-5zm0 7a2 2 0 1 1 0-4 2 2 0 0 1 0 4z" fill="#fff"/></svg>
      <span class="contact__text">Am Feldrain 4 | 6850 Dornbirn</span>
    </div>
    <div class="contact" style="top:219px">
      <svg class="contact__icon" viewBox="0 0 16 16" fill="none" stroke="#fff" stroke-width="1.5"><circle cx="8" cy="8" r="6.5"/><ellipse cx="8" cy="8" rx="2.8" ry="6.5"/><line x1="1.5" y1="8" x2="14.5" y2="8"/><line x1="2.5" y1="4.8" x2="13.5" y2="4.8"/><line x1="2.5" y1="11.2" x2="13.5" y2="11.2"/></svg>
      <span class="contact__text">www.velta-agentur.com</span>
    </div>
    <div class="contact" style="top:253px">
      <svg class="contact__icon" viewBox="0 0 16 16"><rect x="1" y="3" width="14" height="10" fill="#fff"/><polyline points="1,3 8,9 15,3" fill="none" stroke="#013118" stroke-width="1.3"/><line x1="1" y1="13" x2="6" y2="8" stroke="#013118" stroke-width="1"/><line x1="15" y1="13" x2="10" y2="8" stroke="#013118" stroke-width="1"/></svg>
      <span class="contact__text">lukas@velta-agentur.com</span>
    </div>
    <div class="contact" style="top:284px">
      <svg class="contact__icon" style="top:4px" viewBox="0 0 16 16"><path d="M3.6 1.5l2.3 2.6-1.3 2a9 9 0 0 0 5.3 5.3l2-1.3 2.6 2.3-1.4 2.1C7.5 14.9 1.1 8.5 1.5 2.9z" fill="#fff"/></svg>
      <span class="contact__text">+43 5572 41 208 17<br>+43 664 2830 715</span>
    </div>
  </div>
</section>

</body>
</html>
```